Web Design Project for Recipe Search site

Background
Stir The Pages is an internationally (English speaking) focussed website and search engine for cookbooks and recipes for people who love to use great recipes. STP is a unique way to find recipes from ALL sources – both print and digital. STP is the ONLY website that indexes print cookbooks and magazines so a member can easily create a searchable bookshelf of ALL their recipe collection regardless of source. Stir The Pages provides a way to find recipes from any source - it does not provide the complete recipe. You either use the print source - or there is a link if it is available online.
Recently StirThePages created a new home page with a fresh and contemporary design and copy that better captured the essence of the site for potential users. This has improved conversion to membership from that landing page HOWEVER;
The overwhelming majority (60%) of first time visitors to the STP site land on a Library recipe page while they have been searching for a particular recipe. For most this is their first exposure to STP and so they come from a basis of little or no knowledge of the site.

THE BRIEF
Design a page that will be a Pop Up box that appears as a visitor arrives on the Library recipe page Use this link for the page example:
http://www.stirthepages.example/library/recipes/4417302/baked-spiced-apple-wedges-with

AND
Design a modification to the box (currently blue) that is part of the Library recipe page.
The Library recipe page is part of the overall site design and the overall design cannot be changed until a responsive design upgrade is underway. This will be the next project.

Objective
Increase the capture and engagement for STP
Increase the visual impact and Brand Identity for STP
Reduce page bounce and increase conversion into sign on funnel.

Target Market(s)

People who love cooking with great recipes
Our core target is female (70%), aged in her 40s who owns between 40 and 300 cookbooks. She lives in USA, Australia or UK. She loves cookbooks and organization and LOVES cooking great recipes. The reason she loves StirThePages is because she can actually use her cookbooks. We have spoken to thousands of people and these quotes reflect the most frequent feedback about why she love Stir The Pages.
“Stir The Pages is the most exciting thing I’ve found on the internet in ages.”
“It never lets me down when I can’t remember which of my 13 Trevor Lindqvist books a recipe is in.

Industry/Entity Type

Digital

Number of Pages Required

1 page

Requirements
Must have
• Consistent with Home Page - fresh, clean, contemporary, approachable, culinary
• http://www.stirthepages.example/
• Use fonts consistent with existing page - see Style Guide attached.
• http://www.stirthepages.example/library/recipes/4417302/baked-spiced-apple-wedges-with
Nice to have
• Suggested Copy for Pop Up Box
• REDISCOVER YOUR cookbooks
• Join a community of cookbook lovers & discover that Stir The Pages is a great way to make better use of your own collection
• Find any recipe from your own recipe collection in seconds
• Stir The Pages has indexed over 1 million recipes – so now you can have a search engine to find all your recipes in your cookbooks, magazines & favorite blogs
• Connect with a community of like-minded enthusiasts
• Exchange recommendations with other members, discover new ideas & read blogs written by culinary enthusiasts
• Become a member and start organizing your recipes.
• Suggested New copy for Library recipe page
• If this recipe is available online – click on the link “View complete recipe” below
• STP is a recipe search engine for your personal collection. If there’s no link, it means you need to own the book or magazine to see the complete recipe.
• Find out more. (button)
• Join now and get started (button)
Should not have
• Use any new fonts or colors. Stick to colors on site.

```html
<!DOCTYPE html>
<html lang="en">
<head>
<meta charset="utf-8">
<title>Stir The Pages – Recipe Pop Up</title>
<link rel="stylesheet" href="https://fonts.googleapis.com/css2?family=Open+Sans:wght@400;600&family=Overlock:wght@700;900&display=swap">
<style>
:root{
  --green:#5aa02c;
  --orange:#f7a823;
  --grey-btn:#8d8d8d;
  --text:#444;
  --page-bg:#ffffff;
  --panel-bg:#f5f5f5;
  --footer-bg:#fafafa;
  --shade:rgba(0,0,0,.42);
}
*{box-sizing:border-box;margin:0;padding:0}
html,body{width:821px;height:1200px;overflow:hidden}
body{position:relative;background:var(--page-bg);font-family:"Open Sans",sans-serif;color:var(--text)}
.abs{position:absolute}
.site-header{left:0;top:0;width:821px;height:100px;background:#fff;box-shadow:0 2px 4px rgba(0,0,0,.08)}
.brand{left:41px;top:30px;font-size:22px;color:var(--green);font-weight:600;line-height:1}
.brand-mark{display:inline-block;width:14px;height:14px;background:var(--green);margin-right:8px;vertical-align:-1px}
.top-btn{top:30px;height:20px;width:63px;font-size:10px;color:#fff;text-align:center;line-height:20px}
.signup{left:648px;background:var(--orange)}
.login{left:718px;background:var(--green)}
.nav{top:66px;font-size:10px;color:#555}
.nav.active{color:var(--green)}
.hero{left:0;top:100px;width:821px;height:422px;background:#fbfbfb}
.hero-title{left:121px;top:250px;font-family:"Overlock",sans-serif;font-weight:900;font-size:36px;color:#333}
.hero-rule{left:91px;top:301px;width:200px;height:1px;background:var(--green)}
.hero-copy{left:91px;top:312px;font-size:12px;color:#666;line-height:16px}
.hero-photo{left:470px;top:112px;width:290px;height:378px;border-radius:6px;background:linear-gradient(160deg,#d94a2a 0%,#e9c23a 30%,#7aa94a 55%,#c7a06a 75%,#2e2a28 100%)}
.about-title{left:0;top:552px;width:821px;text-align:center;font-size:18px;color:#444}
.about-copy{left:74px;top:588px;width:673px;text-align:center;font-size:8.4px;line-height:13.3px;color:#666}
.small-btn{top:643px;height:20px;font-size:9px;color:#fff;line-height:20px;text-align:center}
.read-more{left:332px;width:75px;background:var(--orange)}
.join-now{left:414px;width:75px;background:var(--green)}
.features{left:41px;top:697px;width:740px;height:148px;background:var(--panel-bg)}
.feature-photo{top:712px;width:178px;height:118px}
.photo-cook{left:55px;background:linear-gradient(120deg,#e8ecef,#c8cfd2 50%,#b9524a)}
.photo-soup{left:420px;background:linear-gradient(135deg,#6b4a34,#8a6446 45%,#e2a12e 60%,#5a3d2a)}
.feature-title{top:707px;width:160px;font-size:13px;line-height:15.5px;color:#555}
.feature-text{width:156px;font-size:7.6px;line-height:10.4px;color:#777}
.cta-band{left:41px;top:884px;width:739px;height:62px;background:var(--green)}
.cta-text{left:155px;top:905px;font-size:15px;color:#eef6e8}
.cta-btn{left:542px;top:904px;width:101px;height:23px;background:var(--orange);color:#fff;font-size:9.6px;line-height:23px;text-align:center}
.footer{left:0;top:946px;width:821px;height:254px;background:var(--footer-bg)}
.col-head{top:985px;font-size:11px;font-weight:600;color:#333}
.col-links{top:1016px;font-size:9.2px;line-height:15.2px;color:#777;list-style:none}
.legal{left:38px;top:1174px;font-size:8.4px;color:#666}
.social{top:1171px;width:12px;height:12px;background:#9aa6b5}
.shade{left:0;top:0;width:821px;height:1200px;background:var(--shade)}
.modal{left:166px;top:208px;width:486px;height:306px;background:#fff}
.close{right:18px;top:14px}
.modal-title{left:0;top:66px;width:486px;text-align:center;font-family:"Overlock",sans-serif;font-weight:900;font-size:25px;letter-spacing:.3px;color:#555}
.modal-copy{left:75px;top:123px;width:336px;text-align:center;font-size:11.4px;line-height:15.3px;color:#444}
.modal-btn{top:206px;width:174px;height:31px;color:#fff;font-family:"Overlock",sans-serif;font-weight:700;font-size:12.5px;line-height:31px;text-align:center;letter-spacing:.3px}
.find-out{left:65px;background:var(--grey-btn)}
.get-started{left:248px;background:var(--orange)}
</style>
</head>
<body>
<header class="abs site-header">
  <div class="abs brand"><span class="brand-mark"></span>Stir The Pages</div>
  <div class="abs top-btn signup">Signup</div>
  <div class="abs top-btn login">Login</div>
  <div class="abs nav active" style="left:447px">Home</div>
  <div class="abs nav" style="left:512px">Forum</div>
  <div class="abs nav" style="left:579px">Blog</div>
  <div class="abs nav" style="left:635px">About Us</div>
  <div class="abs nav" style="left:714px">Contact|Help</div>
</header>

<section class="abs hero"></section>
<div class="abs hero-title">COOKBOOKS</div>
<div class="abs hero-rule"></div>
<div class="abs hero-copy">Join a community of cookbook lovers &amp;<br>Stir The Pages is a great way to make</div>
<div class="abs hero-photo" role="img" aria-label="Stack of cookbooks topped with fresh vegetables and fruit"></div>

<div class="abs about-title">About Us</div>
<p class="abs about-copy">Stir The Pages is a website for people who love cookbooks and love to use great recipes. If you have a cookbook collection, you probably get a lot of pleasure from browsing your books - but there are times when you haven't got time to look through them all to find a recipe. Or maybe you feel you're not using them as effectively as you'd like, sticking to familiar recipes or not branching beyond the current favorites.</p>
<div class="abs small-btn read-more">Read More</div>
<div class="abs small-btn join-now">Join Now</div>

<div class="abs features"></div>
<div class="abs feature-photo photo-cook" role="img" aria-label="Woman cooking in a bright kitchen with a cookbook open"></div>
<div class="abs feature-title" style="left:243px">Find any recipe from your own recipe collection in seconds</div>
<p class="abs feature-text" style="left:243px;top:762px">Stir The Pages has indexed over 1 million recipes – so now you can have a search engine to find all your recipes in your cookbooks, magazines &amp; favorite blogs</p>
<div class="abs feature-photo photo-soup" role="img" aria-label="Bowl of pumpkin soup with herbs and a spoon on a wooden table"></div>
<div class="abs feature-title" style="left:607px;width:170px">Connect with a community of like-minded enthusiasts</div>
<p class="abs feature-text" style="left:608px;top:762px;width:157px">Exchange recommendations with other members, discover new ideas &amp; read blogs written by culinary enthusiasts</p>

<div class="abs cta-band"></div>
<div class="abs cta-text">Become a member and start organizing your recipes.</div>
<div class="abs cta-btn">JOIN FOR FREE</div>

<footer class="abs footer"></footer>
<div class="abs col-head" style="left:43px">THE BEST RECIPES</div>
<ul class="abs col-links" style="left:43px"><li>Chicken</li><li>Fruit Tarts</li><li>Meatballs</li><li>Vegetarian Pasta</li><li>Chocolate Cakes</li><li>Gluten Free Baking</li><li>Breakfast</li><li>Pumpkin</li></ul>
<div class="abs col-head" style="left:241px">THE BEST AUTHORS</div>
<ul class="abs col-links" style="left:241px"><li>Ravi Castellano</li><li>Owen Brightwater</li><li>Delia Harrow</li><li>Marisol Kettering</li><li>Celeste Duvernay</li><li>Ruth Ellery Bannister</li><li>Iris Galloway</li><li>Trevor Lindqvist</li></ul>
<div class="abs col-head" style="left:446px">THE BEST COOKBOOKS</div>
<ul class="abs col-links" style="left:446px"><li>New Cookbooks</li><li>Most Popular Cookbooks</li><li>Indexed Baking Cookbooks</li><li>Indexed BBQ Cookbooks</li><li>Indexed Vegetarian Cookbooks</li><li>Index Test Kitchen Quarterly Cookbooks</li><li>Kitchens Abroad Series</li><li>Best Cookbooks of 2013</li></ul>
<div class="abs col-head" style="left:684px">STIR THE PAGES</div>
<ul class="abs col-links" style="left:684px"><li>Quick Tour</li><li>Member Benefits</li><li>Getting Started</li><li>About Stir The Pages</li><li>Support Page</li><li>Email Preferences</li><li>Terms of Use</li><li>Privacy</li></ul>
<div class="abs legal">©2015 yoursite - Terms of Service - Privacy - Program Policies</div>
<div class="abs social" style="left:702px"></div>
<div class="abs social" style="left:724px"></div>
<div class="abs social" style="left:746px"></div>
<div class="abs social" style="left:767px"></div>

<div class="abs shade"></div>

<div class="abs modal" role="dialog" aria-labelledby="modal-title">
  <svg class="abs close" width="11" height="11" viewBox="0 0 11 11" aria-label="Close"><path d="M1.5 1.5l8 8M9.5 1.5l-8 8" stroke="#777" stroke-width="2.4" stroke-linecap="round"/></svg>
  <h2 id="modal-title" class="abs modal-title">If this recipe is available online</h2>
  <p class="abs modal-copy">STP is a recipe search engine for your personal collection. If there’s no link, it means you need to own the book or magazine to see the complete recipe.</p>
  <div class="abs modal-btn find-out">Find Out More</div>
  <div class="abs modal-btn get-started">Join Now &amp; Get Started</div>
</div>
</body>
</html>
```